Attractive Flyer for Moving Company

Our Company called "Harborlight Moving Company".
We provide moving service for home and businesses
We need a flyer for a moving company, located in San Diego, CA USA
Flyer size will be 7 x 5 inches, double sided.

Flyer needs to be very attractive and catchy for eye. I want people to keep it even if they dont need our service. I attached a lot of text in separate word file.
Logo, brief and additional pictures are attached.

Target Market(s)

27 years - 55 Years old

Industry/Entity Type

Moving Company

Colors
ec1f27
3176b5
ffffff

Requirements
Must have
• Attached in Word File
Nice to have
• Please be creative in placing a text and selecting a back ground picture.

```html
<!DOCTYPE html>
<html lang="en">
<head>
<meta charset="utf-8">
<title>Harborlight Moving Company – Flyer</title>
<link rel="stylesheet" href="https://fonts.googleapis.com/css2?family=Montserrat:ital,wght@0,400;0,600;0,700;0,800;1,600&family=Open+Sans:wght@400;600&display=swap">
<style>
:root{
  --red:#e31e26;
  --red-deep:#a9111a;
  --blue:#0d4a8a;
  --blue-deep:#163a73;
  --white:#ffffff;
  --ink:#444444;
  --stage:#3b3b3b;
  --gold:#d9a521;
}
*{box-sizing:border-box;margin:0;padding:0}
html,body{width:867px;height:1200px;overflow:hidden;background:var(--stage)}
body{position:relative;font-family:"Montserrat",sans-serif}
.side{position:absolute;left:47px;width:766px;height:547px;background:var(--white);overflow:hidden}
.side--front{top:37px}
.side--back{top:613px}
.abs{position:absolute}

/* front */
.brand{left:25px;top:30px;color:var(--red);font-weight:800;line-height:1}
.brand__name{font-size:31px;letter-spacing:-.5px}
.brand__sub{font-size:14px;margin-top:6px;letter-spacing:.5px}
.brand__mark{display:inline-block;width:14px;height:14px;background:var(--red);border-radius:50%;margin-right:6px;vertical-align:2px}
.tagline{left:306px;top:24px;font-style:italic;font-weight:600;font-size:17px;line-height:1.15;color:var(--blue)}
.tagline em{color:var(--red);font-style:italic}
.license{left:306px;top:80px;font-family:"Open Sans",sans-serif;font-size:10px;line-height:1.35;color:#333}
.badge-rect{left:633px;top:21px;width:43px;height:68px;background:var(--blue);border-radius:3px}
.badge-circle{left:683px;top:26px;width:59px;height:59px;border-radius:50%;background:var(--red-deep)}
.photo-main{left:0;top:130px;width:766px;height:417px;background:linear-gradient(100deg,#c9a57a 0%,#dcc3a0 35%,#8fa9c9 60%,#d8c0a0 100%)}
.seal{left:618px;top:108px;width:118px;height:118px;border-radius:50%;background:radial-gradient(circle,#f4cf5a 0%,var(--gold) 70%,#a8780f 100%)}
.pennant{left:26px;top:136px;width:262px;height:206px}
.pennant__text{left:26px;top:145px;width:262px;text-align:center;color:var(--white)}
.pennant__head{font-weight:800;font-size:27px}
.pennant__lead{font-size:18px;margin-top:6px;line-height:1.1}
.pennant__deal{font-weight:700;font-size:18px;line-height:1.1}
.pennant__note{font-size:11px}
.pennant__ask{font-weight:700;font-size:16px;margin-top:8px}
.pennant__keep{font-size:17px;line-height:1}
.front-band{left:0;top:415px}
.refer{left:41px;top:472px;color:var(--white);font-weight:700;font-size:23px;line-height:1.35}
.front-web{left:459px;top:514px;color:var(--white);font-weight:700;font-size:15px}

/* back */
.save{left:25px;top:30px;font-weight:800;font-size:50px;line-height:1.18;color:var(--blue)}
.save span{color:var(--red-deep)}
.deals-title{left:25px;top:158px;font-weight:700;font-size:33px;color:var(--red-deep)}
.deals-note{left:25px;top:199px;font-size:14.5px;color:var(--ink)}
.promo{left:25px;top:224px;font-weight:800;font-size:21px;color:var(--blue);display:flex;align-items:center;gap:12px}
.promo__code{background:var(--red-deep);color:var(--white);padding:0 6px;height:27px;line-height:27px;font-weight:700}
.offer{top:268px;width:228px;height:98px;border:2px dashed var(--blue);border-radius:8px;text-align:center;color:#555}
.offer--two{left:25px}
.offer--three{left:265px}
.offer__price{font-weight:800;font-size:36px;color:var(--red-deep);line-height:1.1}
.offer__desc{font-size:13.5px;line-height:1.2}
.offer__card{font-size:10px;margin-top:1px}
.longd{left:25px;top:380px;font-weight:700;font-size:25px;color:var(--red-deep)}
.boxes{left:25px;top:417px;font-size:18px;color:var(--blue)}
.valid{left:25px;top:446px;font-family:"Open Sans",sans-serif;font-size:12px;color:#333}
.photo-couple{left:515px;top:29px;width:221px;height:152px;background:linear-gradient(120deg,#ece6dc 0%,#c7b7a0 45%,#6c8fbf 60%,#e6a3b4 85%)}
.photo-couple::before{content:"";position:absolute;left:0;top:-3px;width:100%;height:3px;background:var(--blue-deep)}
.included{left:515px;top:193px;font-weight:800;font-size:21px;color:var(--red-deep)}
.incl-list{left:515px;top:225px;width:225px;font-size:13px;line-height:1.27;color:var(--ink);list-style:none}
.incl-list li{position:relative;padding-left:20px}
.incl-list li::before{content:"";position:absolute;left:5px;top:6px;width:5px;height:5px;border-radius:50%;background:var(--blue)}
.terms{left:515px;top:341px;width:233px;height:121px;background:var(--blue-deep);color:var(--white);font-size:13px;line-height:1.3;text-align:center;padding:10px 6px}
.back-band{left:0;top:448px}
.back-web{left:25px;top:513px;color:var(--white);font-weight:700;font-size:18px}
.call{right:37px;top:478px;text-align:right;color:var(--white)}
.call__lead{font-size:16px}
.call__num{font-weight:800;font-size:20px}
</style>
</head>
<body>

<section class="side side--front" aria-label="Flyer front">
  <div class="abs photo-main" role="img" aria-label="Photo of a smiling young couple sitting among moving boxes"></div>
  <svg class="abs" style="left:0;top:0" width="766" height="190" viewBox="0 0 766 190" aria-hidden="true">
    <path d="M0 190 L0 0 L766 0 L766 120 C600 150 420 135 300 140 C150 145 60 160 0 190Z" fill="#fff"/>
    <path d="M0 180 C70 155 170 140 330 142" fill="none" stroke="#163a73" stroke-width="8"/>
    <path d="M540 148 C620 145 700 135 766 122" fill="none" stroke="#163a73" stroke-width="4"/>
  </svg>

  <div class="abs brand">
    <div class="brand__name"><span class="brand__mark"></span>Harborlight</div>
    <div class="brand__sub">MOVING COMPANY</div>
  </div>
  <p class="abs tagline"><em>Quality Focused,</em> Customer<br>Recommended Movers</p>
  <p class="abs license">Licensed &amp; Fully Insured,<br>CAL PUC: #204718 US DOT: #30562294</p>
  <div class="abs badge-rect" role="img" aria-label="Accreditation badge"></div>
  <div class="abs badge-circle" role="img" aria-label="Review site badge"></div>
  <div class="abs seal" role="img" aria-label="Satisfaction guarantee seal"></div>

  <svg class="abs pennant" viewBox="0 0 262 206" aria-hidden="true">
    <path d="M0 0 H262 V140 L131 206 L0 140Z" fill="#fff"/>
    <path d="M0 0 H262 V132 L131 194 L0 132Z" fill="var(--red)"/>
  </svg>
  <div class="abs pennant__text">
    <p class="pennant__head">Need MOVERS?</p>
    <p class="pennant__lead">Take advantage of our</p>
    <p class="pennant__deal">SPECIAL DEALS</p>
    <p class="pennant__note">(see reverse side).</p>
    <p class="pennant__ask">Not moving soon?</p>
    <p class="pennant__keep">Keep this flyer<br>for later.</p>
  </div>

  <svg class="abs front-band" width="766" height="132" viewBox="0 0 766 132" aria-hidden="true">
    <path d="M0 20 C200 -5 450 40 766 100 V132 H0Z" fill="#163a73"/>
    <path d="M0 30 C200 8 450 50 766 108 V132 H0Z" fill="var(--red)"/>
  </svg>
  <p class="abs refer">Know someone who is moving?<br>Let them know about our deals</p>
  <p class="abs front-web">www.HarborlightMoving.com</p>
</section>

<section class="side side--back" aria-label="Flyer back">
  <h1 class="abs save">SAVE <span>15% -25%</span><br>ON YOUR MOVE</h1>
  <h2 class="abs deals-title">Special Deals</h2>
  <p class="abs deals-note">(Cannot be used with any other promotions or coupons)</p>
  <p class="abs promo">PROMOTION CODE: <span class="promo__code">HMC1016</span></p>

  <div class="abs offer offer--two">
    <p class="offer__price">$235</p>
    <p class="offer__desc">3 hours of Moving Service with<br>2 PRO MOVERS &amp; TRUCK</p>
    <p class="offer__card">*$265 if paid with card</p>
  </div>
  <div class="abs offer offer--three">
    <p class="offer__price">$325</p>
    <p class="offer__desc">3 hours of Moving Service with<br>3 PRO MOVERS &amp; TRUCK</p>
    <p class="offer__card">*$355 if paid with card</p>
  </div>

  <p class="abs longd">$75 off any Long Distance Move</p>
  <p class="abs boxes">+ 20% OFF for boxes and packing supplies.</p>
  <p class="abs valid">Keep this voucher it is valid until January 1, 2020</p>

  <div class="abs photo-couple" role="img" aria-label="Photo of a happy older couple sitting back to back among moving boxes"></div>
  <h3 class="abs included">INCLUDED IN PRICE</h3>
  <ul class="abs incl-list">
    <li>Protection of your furniture withspecialized blankets and plastic stretch wrap.</li>
    <li>Disassembly and reassembly of your furniture.</li>
    <li>Use of Wardrobe boxes</li>
  </ul>
  <p class="abs terms">*Promotion code must be provided to our representative when requesting a quote and booking service appointment. *Promotion is valid for the first time customers ONLY</p>

  <svg class="abs back-band" width="766" height="99" viewBox="0 0 766 99" aria-hidden="true">
    <path d="M0 15 C200 40 500 30 766 0 V99 H0Z" fill="#163a73"/>
    <path d="M0 22 C200 48 500 38 766 8 V99 H0Z" fill="var(--red)"/>
  </svg>
  <p class="abs back-web">www.HarborlightMoving.com</p>
  <div class="abs call">
    <p class="call__lead">Call For A Quick Estimate</p>
    <p class="call__num">Toll Free: 1-855-555-0147</p>
  </div>
</section>

</body>
</html>
```